Investment company needing business card

We are wanting a business card which looks sharp and easy on the eye. We are thinking of having a business card with the logo embossed on it, to really make it stand out. We will only have a small amount of information of the business card, person's name, position, email address and phone number

Contact Information for Business Card

Danielle Frost
Executive Assistant
+64 21 473 5162
danielf@harwickpartners.co.nz

Requirements
Must have
• Embossed logo
Should not have
• Not to be busy

```html
<!DOCTYPE html>
<html lang="en">
<head>
<meta charset="UTF-8">
<title>Harwick Partners – Business Card</title>
<link href="https://fonts.googleapis.com/css2?family=Roboto+Condensed:wght@500;700&family=Roboto:wght@400&display=swap" rel="stylesheet">
<style>
  :root {
    --backdrop: #1c1c1c;
    --card: #f4f4f4;
    --brand-green: #2bb673;
    --ink-grey: #5e5e5e;
    --mark-grey: #5a5a5a;
    --emboss-light: #ffffff;
    --emboss-shade: rgba(0,0,0,0.13);
  }
  html, body {
    margin: 0;
    width: 1200px;
    height: 960px;
    overflow: hidden;
    background: var(--backdrop);
  }
  .business-card {
    position: absolute;
    left: 300px;
    top: 309px;
    width: 600px;
    height: 343px;
    background: var(--card);
    box-shadow: 0 3px 10px rgba(0,0,0,0.45);
  }
  .brand {
    position: absolute;
    left: 60px;
    top: 64px;
    display: flex;
    align-items: center;
    gap: 12px;
  }
  .brand-square {
    width: 48px;
    height: 48px;
    background: var(--mark-grey);
  }
  .brand-name {
    font-family: "Roboto Condensed", sans-serif;
    font-weight: 700;
    font-size: 26px;
    letter-spacing: 0.5px;
    color: var(--brand-green);
  }
  .contact {
    position: absolute;
    left: 59px;
    top: 178px;
  }
  .contact-name {
    margin: 0;
    font-family: "Roboto Condensed", sans-serif;
    font-weight: 700;
    font-size: 21px;
    line-height: 24px;
    color: var(--brand-green);
  }
  .contact-role {
    margin: 0 0 16px;
    font-family: "Roboto Condensed", sans-serif;
    font-weight: 500;
    font-size: 16px;
    line-height: 20px;
    color: var(--ink-grey);
  }
  .contact-line {
    margin: 0;
    font-family: "Roboto", sans-serif;
    font-size: 14.5px;
    line-height: 18.5px;
    color: var(--ink-grey);
  }
  .embossed-mark {
    position: absolute;
    left: 392px;
    top: 170px;
  }
</style>
</head>
<body>
  <div class="business-card">
    <div class="brand">
      <div class="brand-square"></div>
      <div class="brand-name">HARWICK PARTNERS</div>
    </div>

    <div class="contact">
      <p class="contact-name">DANIELLE FROST</p>
      <p class="contact-role">EXECUTIVE ASSISTANT</p>
      <p class="contact-line">+64 21 473 5162</p>
      <p class="contact-line">danielf@harwickpartners.co.nz</p>
      <p class="contact-line">www.harwickpartners.co.nz</p>
    </div>

    <svg class="embossed-mark" width="146" height="134" viewBox="0 0 146 134" aria-hidden="true">
      <rect x="2" y="2" width="142" height="130" rx="4" fill="none" stroke="var(--emboss-light)" stroke-width="2"/>
      <rect x="1" y="1" width="142" height="130" rx="4" fill="var(--card)" stroke="var(--emboss-shade)" stroke-width="1.5"/>
    </svg>
  </div>
</body>
</html>
```